Flat bootstrap design for existing site

I'm looking for a modern flat design based around an existing logo. This has to be a custom design (no external templates), and implemented into a bootstrap framework.

The logo is attached as 2 versions - choose whichever you want, that flows better with whatever design you choose.

Added screenshots of the existing site (currently using the default bootstrap layouts). Please make your designs around those pages in the screenshots (i.e. the homepage only has the postal code input and the header). The active page has 3 screenshots, because I wanted to illustrate the other states that would be visible (in the table rows).

This is a moving/junk removal website, just for some context.

Here's some example websites (flat designs) that I like, just to give you an idea of what I'm after.

https://www.plimvora.com/
https://dacklow.com/
https://trevanu.com/
https://quobrintal.com/en/

Coding

Coded - Design and coding required

Number of Pages Required

5+ page

Colors

Designer to choose colors to be used in the design.

Requirements
Must have
• It must be a modern/simple flat design, that is built around the existing logo (attached).
• It has to be implemented using bootstrap.

```html
<!DOCTYPE html>
<html lang="en">
<head>
<meta charset="utf-8">
<title>Bravolt — Sign In</title>
<link rel="stylesheet" href="https://fonts.googleapis.com/css2?family=Roboto:wght@400;500;700&display=swap">
<style>
  :root {
    --brand-blue: #4bc9f5;
    --brand-blue-active: #3fb8e2;
    --page-bg: #f7f7f7;
    --card-bg: #ffffff;
    --card-border: #dcdcdc;
    --input-border: #cfcfcf;
    --heading: #555555;
    --placeholder: #777777;
    --footer-bg: #5a5a5a;
    --white: #ffffff;
  }
  * { box-sizing: border-box; margin: 0; padding: 0; }
  html, body {
    width: 1200px; height: 557px; overflow: hidden;
    background: var(--page-bg);
    font-family: "Roboto", Arial, sans-serif;
  }
  .site-header {
    height: 88px; background: var(--brand-blue);
    position: relative;
  }
  .brand {
    position: absolute; left: 87px; top: 24px;
    display: flex; align-items: center; gap: 10px;
    color: var(--white); font-weight: 700; font-size: 34px; letter-spacing: 1px;
    text-transform: uppercase;
  }
  .brand-dot {
    width: 22px; height: 22px; border-radius: 50%; background: var(--white);
  }
  .main-nav {
    position: absolute; right: 0; top: 0; height: 88px;
    display: flex; padding-right: 104px;
  }
  .main-nav a {
    display: flex; align-items: center; height: 88px; padding: 0 29px;
    color: var(--white); text-decoration: none;
    font-size: 13px; font-weight: 500; text-transform: uppercase;
  }
  .main-nav a.is-active { background: var(--brand-blue-active); }
  .signin-card {
    position: absolute; left: 86px; top: 150px; width: 1028px; height: 274px;
    background: var(--card-bg); border: 1px solid var(--card-border); border-radius: 3px;
  }
  .signin-title {
    text-align: center; margin-top: 34px;
    font-size: 20px; font-weight: 400; color: var(--heading);
  }
  .signin-form {
    width: 302px; margin: 18px auto 0;
    display: flex; flex-direction: column; gap: 9px;
  }
  .field {
    height: 43px; border: 1px solid var(--input-border); border-radius: 3px;
    padding: 0 15px; font-family: Arial, sans-serif; font-size: 13px; color: var(--placeholder);
    background: var(--white); outline: none;
  }
  .field::placeholder { color: var(--placeholder); }
  .btn-login {
    height: 43px; border: none; border-radius: 3px;
    background: var(--brand-blue); color: var(--white);
    font-family: "Roboto", sans-serif; font-size: 14px; font-weight: 500; text-transform: uppercase;
  }
  .site-footer {
    position: absolute; left: 0; top: 489px; width: 1200px; height: 68px;
    background: var(--footer-bg);
  }
  .copyright {
    position: absolute; left: 87px; top: 25px;
    color: var(--white); font-size: 12px; font-weight: 500;
  }
  .social-links {
    position: absolute; left: 942px; top: 18px;
    display: flex; gap: 5px; list-style: none;
  }
  .social-links li {
    width: 30px; height: 30px; border: 1.5px solid var(--white); border-radius: 50%;
  }
</style>
</head>
<body>
  <header class="site-header">
    <div class="brand"><span class="brand-dot"></span>Bravolt</div>
    <nav class="main-nav">
      <a href="#">Book</a>
      <a href="#">How it works</a>
      <a href="#" class="is-active">Become a driver</a>
      <a href="#">Sign in</a>
    </nav>
  </header>

  <main class="signin-card">
    <h1 class="signin-title">PLEASE SIGN IN</h1>
    <form class="signin-form">
      <input class="field" type="email" placeholder="Email Address:">
      <input class="field" type="password" placeholder="Password :">
      <button class="btn-login" type="button">Login</button>
    </form>
  </main>

  <footer class="site-footer">
    <p class="copyright">© Copyright 2017 Bravolt.All Rights Reserved.</p>
    <ul class="social-links" aria-label="Social links">
      <li></li><li></li><li></li><li></li><li></li>
    </ul>
  </footer>
</body>
</html>
```